Bluebird Stage Retreats 2016 Brochure

Hi there! Bluebird Stage Retreats (www.BluebirdStageRetreats.example) operates overnight dance camps for girls ages 8 - 17 in eight U.S. states. We need a designer to help us create our 2016 brochure.

Most prospective camper families will download the brochure through our website, but some may also request to have a print version sent via mail, so the brochure will need to be print quality.

We'd like the brochure to be similar to our 2015 brochure (attached, both print & web), just with new pictures & correct dates/rates/offers. Also, we recently migrated our website to wordpress, so we'd like the brochure to have a similar look/feel to our new site in terms of fonts, colors, etc.

Using the attached program as a template, I'd love to have designers submit a mock up for our 2016 cover as well as a couple inside pages.

Newer pictures can be accessed online:
Flickr username: marla_quibbet / pw: Harriet5678
Instagram: @stagebsrx

The fonts on our website are "Mountains of Christmas" and "PT Sans". Attached are a couple higher quality versions of our logo as well.

Also, just want to mention that I'm looking to develop a longer-term relationship with a designer - many projects in the pipeline :-)

Thanks!

Paulette
pkorvish@stagebsrx.example

```html
<!DOCTYPE html>
<html lang="en">
<head>
<meta charset="utf-8">
<title>Special Offers and Referral Program – Bluebird Stage Retreats</title>
<link rel="stylesheet" href="https://fonts.googleapis.com/css2?family=Mountains+of+Christmas:wght@700&family=PT+Sans:wght@400;700&display=swap">
<style>
  :root {
    --plum: #93356a;
    --lime: #b1d57a;
    --ink: #1a1a1a;
    --paper: #ffffff;
    --photo-top: #d9c7bf;
    --photo-bottom: #9c8a96;
  }
  * { box-sizing: border-box; margin: 0; padding: 0; }
  html, body {
    width: 1200px;
    height: 1099px;
    overflow: hidden;
    background: var(--paper);
  }
  .page {
    position: relative;
    width: 1200px;
    height: 1099px;
    font-family: "PT Sans", Arial, sans-serif;
    color: var(--ink);
  }
  .header-band {
    position: absolute;
    left: 0;
    top: 25px;
    width: 1200px;
    height: 168px;
    background: var(--lime);
  }
  .header-title {
    position: absolute;
    left: 251px;
    top: 0;
    width: 949px;
    height: 168px;
    background: var(--plum);
    color: var(--paper);
    font-family: "Mountains of Christmas", cursive;
    font-weight: 700;
    font-size: 58px;
    display: flex;
    align-items: center;
    justify-content: center;
    padding-bottom: 8px;
  }
  .campers-photo {
    position: absolute;
    left: 227px;
    top: 227px;
    width: 914px;
    height: 391px;
    background: linear-gradient(180deg, var(--photo-top), var(--photo-bottom));
  }
  .section-heading {
    position: absolute;
    left: 59px;
    top: 618px;
    width: 540px;
    height: 70px;
    background: var(--lime);
    color: var(--plum);
    font-weight: 700;
    font-size: 52px;
    line-height: 70px;
    padding-left: 6px;
    letter-spacing: 0.5px;
  }
  .intro {
    position: absolute;
    left: 59px;
    top: 713px;
    font-size: 19px;
  }
  .savings-list {
    position: absolute;
    left: 59px;
    top: 763px;
    width: 1080px;
    display: grid;
    grid-template-columns: 171px 1fr;
    column-gap: 4px;
    font-size: 18.5px;
    line-height: 30px;
  }
  .savings-name {
    color: var(--plum);
    font-weight: 700;
    text-align: right;
  }
  .savings-detail {
    padding-left: 0;
  }
  .savings-detail .wrap {
    display: block;
    padding-left: 10px;
  }
</style>
</head>
<body>
<main class="page">
  <div class="header-band"></div>
  <h1 class="header-title">Special Offers and Referral Program</h1>

  <div class="campers-photo" role="img" aria-label="Group photo of smiling campers making playful faces"></div>

  <h2 class="section-heading">ADDITIONAL SAVINGS</h2>
  <p class="intro">You may qualifiy for added savings on your BSR tuition:</p>

  <dl class="savings-list">
    <dt class="savings-name">Alumni Discount:</dt>
    <dd class="savings-detail">$50 OFF Tuition, per-camper / per-session (Applies to BSR alumni campers only)</dd>

    <dt class="savings-name">Sibling Discount:</dt>
    <dd class="savings-detail">$50 OFF Tuition, per-camper (Campers must be from the same household)</dd>

    <dt class="savings-name">Friend Discount:</dt>
    <dd class="savings-detail">$25 Canteen Credit, per-camper (Applies to EACH friend you refer who enrolls. You BOTH get a credit)</dd>

    <dt class="savings-name">Partner Discount:</dt>
    <dd class="savings-detail">$50 OFF Tuition, per-camper / per-session (Applies to EACH friend you refer who enrolls. You BOTH get<span class="wrap">discount (in addition to a $25 Canteen Credit)</span></dd>

    <dt class="savings-name">Director Discount:</dt>
    <dd class="savings-detail">$100 OFF Tuition, per-camper / per-session (Applies to EACH friend you refer who enrolls. You BOTH get<span class="wrap">discount (in addition to a $25 Canteen Credit)</span></dd>
  </dl>
</main>
</body>
</html>
```